Harborview Estates Business Card for Apartment Buildings

Create business cards for resident managers who run apartment buildings. The audience is the public who are searching for apartment rentals, and current residents who live at the apartment building. Key design element will be incorporating the company logo, however, the logo cannot dominate. The building name and manager name are more important than the logo. Current business card design leaves little room for copy, so we may need to reduce the size on the current card to allow for more space for copy.

Target Market(s)

Adults 18-65 years of age, who are looking for an apartment rental, plus current residents who live at our apartment buildings.

Industry/Entity Type

Property Management

Contact Information for Business Card

A major design element will be use of the company logo. Important property and manager contact information must be part of the design. The size of the logo will need to be reduced to make room for building and manager contact copy.

Font styles to use
Sans Serif

Colors
3176b5
000000
959595
ffffff

Requirements
Must have
• 1) Incorporate the company logo.
• 2) Use the company colors (dark blue, black/grey, over white).
• 3) FEATURE THE BUILDING NAME
• 4) FEATURE THE MANAGER NAME
• 5) The company name is less important than BUILDING and MANAGER
• 6) Manager contact information
• **SEE ATTACHED CREATIVE BRIEF**
Nice to have
• 1) Back of card logo watermark
• 2) Ability to write notes on back of carfd
Should not have
• Avoid letting the company logo dominate the card, the building name and manager are more important than the company logo.

```html
<!DOCTYPE html>
<html lang="en">
<head>
<meta charset="utf-8">
<title>Harborview Estates – Resident Manager Business Card</title>
<link rel="stylesheet" href="https://fonts.googleapis.com/css2?family=Lato:wght@300;400;700;900&display=swap">
<style>
  :root {
    --brand-blue: #3176b5;
    --ink: #000000;
    --ink-soft: #222222;
    --grey: #959595;
    --paper: #ffffff;
    --stage: #e4e6e7;
    --watermark: #e6e6e8;
  }
  * { box-sizing: border-box; margin: 0; padding: 0; }
  html, body {
    width: 1200px; height: 1000px; overflow: hidden;
    background: var(--stage);
    font-family: "Lato", Arial, sans-serif;
  }
  .card {
    position: absolute;
    left: 320px;
    width: 560px; height: 320px;
    background: var(--paper);
    overflow: hidden;
    box-shadow: 0 4px 14px rgba(0,0,0,.18);
  }
  .card--front { top: 135px; }
  .card--back  { top: 545px; }

  /* ---------- front: header ---------- */
  .header {
    position: absolute; left: 0; top: 0;
    width: 100%; height: 150px;
    background: var(--paper);
    box-shadow: 0 3px 6px rgba(0,0,0,.12);
  }
  .brand-block {
    position: absolute; left: 0; top: 40px;
    width: 100px; height: 110px;
    background: var(--brand-blue);
  }
  .brand-circle {
    position: absolute; left: 38px; top: 50px;
    width: 88px; height: 88px; border-radius: 50%;
    background: var(--paper);
    border: 4px solid #d7d9db;
    box-shadow: 0 2px 5px rgba(0,0,0,.25);
  }
  .company-name {
    position: absolute; left: 142px; top: 22px;
    font-weight: 900; font-size: 27px; letter-spacing: .5px;
    color: var(--brand-blue); line-height: 1;
    white-space: nowrap;
  }
  .company-rule {
    position: absolute; left: 142px; top: 60px;
    width: 340px; height: 3px; background: var(--brand-blue);
  }
  .building-name {
    position: absolute; left: 142px; top: 78px;
    font-weight: 700; font-size: 20px; color: var(--ink-soft);
    white-space: nowrap;
  }
  .building-address {
    position: absolute; left: 142px; top: 106px;
    font-weight: 400; font-size: 15.5px; color: var(--ink-soft);
    white-space: nowrap;
  }
  .building-address .sep { color: var(--grey); padding: 0 6px; }

  /* ---------- front: manager ---------- */
  .manager {
    position: absolute; left: 48px; top: 192px;
  }
  .manager-first {
    font-weight: 300; font-size: 23px; letter-spacing: .5px;
    color: #555; line-height: 1.1;
  }
  .manager-last {
    font-weight: 900; font-size: 25px; color: var(--ink-soft); line-height: 1.1;
  }
  .manager-title {
    font-weight: 300; font-size: 15px; color: #777; margin-top: 4px;
  }
  .divider {
    position: absolute; left: 300px; top: 175px;
    width: 2px; height: 105px; background: var(--brand-blue);
  }
  .contact {
    position: absolute; left: 322px; top: 182px;
    list-style: none;
    font-size: 15px; color: var(--ink-soft); line-height: 22px;
    white-space: nowrap;
  }

  /* ---------- back ---------- */
  .watermark {
    position: absolute; inset: 0;
    display: flex; align-items: center; justify-content: center;
    gap: 22px;
  }
  .watermark-circle {
    flex: none;
    width: 110px; height: 110px; border-radius: 50%;
    border: 14px solid var(--watermark);
  }
  .watermark-name {
    font-weight: 900; font-size: 30px; letter-spacing: 1px;
    color: var(--watermark); white-space: nowrap;
  }
</style>
</head>
<body>

  <section class="card card--front" aria-label="Business card front">
    <div class="header">
      <div class="brand-block"></div>
      <div class="brand-circle"></div>
      <div class="company-name">HARBORVIEW ESTATES</div>
      <div class="company-rule"></div>
      <div class="building-name">Cedar Grove Apartments</div>
      <div class="building-address">1482 Linden Avenue<span class="sep">|</span>Port Ellis, CA 90210</div>
    </div>

    <div class="manager">
      <div class="manager-first">MARISOL</div>
      <div class="manager-last">VEGA</div>
      <div class="manager-title">Resident Manager</div>
    </div>
    <div class="divider"></div>
    <ul class="contact">
      <li>O: 555-014-2210</li>
      <li>F: 555-014-3377</li>
      <li>C: 555-014-8840</li>
      <li>E: marisol@harborviewest.com</li>
    </ul>
  </section>

  <section class="card card--back" aria-label="Business card back">
    <div class="watermark">
      <div class="watermark-circle"></div>
      <div class="watermark-name">HARBORVIEW ESTATES</div>
    </div>
  </section>

</body>
</html>
```